New Business Card Design Project

I need a design for business cards, i am an electrical business called "Corvane Electrical and Communications" i need the cards to be double sided with the company logo on the back (attached) the front needs to say my company name, web site, email address, telephone number, and ABN number and electrical license number. I am open to different arrangements of the information but would like the background to be incorporating something electrical or something that looks smart. open to all additional ideas also.

The company colours are orange and grey see logo attached.

Business Name: Corvane Electrical and Communications
Website: corvaneelectricalandcomms.example.com.au
Email: brent@corvaneelectricalandcomms.example.com.au
Telephone(mobile): 0481209736
ABN: 71208349162
Lic No: 418273D

Target Market(s)

Business entities, Project Managers, Accounts, Clients

Industry/Entity Type

Electrician

Contact Information for Business Card

I need a design for business cards, i am an electrical business called "Corvane Electrical and Communications" i need the cards to be double sided with the company logo on the back (attached) the front needs to say my company name

Font styles to use
Serif
Sans Serif

Colors
f37122
5c5c5c

Requirements
Must have
• Must have the Logo on the back open to different ways of it being on the back but had in mind to keep it central but again open to other options
Nice to have
• A real modern cool background that is eye catching yet contemporary
Should not have
• No backgrounds of a light bulb or plug or anything like that

```html
<!DOCTYPE html>
<html lang="en">
<head>
<meta charset="utf-8">
<title>Corvane Electrical and Communications – Business Card</title>
<link rel="stylesheet" href="https://fonts.googleapis.com/css2?family=Exo+2:wght@400;600;700&display=swap">
<style>
  :root {
    --orange: #f37122;
    --grey: #5c5c5c;
    --card-dark: #2e2e30;
    --card-mid: #505053;
    --card-light: #a7a6a4;
    --text-light: #e8e8e8;
    --text-dark: #1e1e1e;
    --page-bg: #e7e4e0;
  }
  * { box-sizing: border-box; margin: 0; padding: 0; }
  html, body {
    width: 1200px;
    height: 969px;
    overflow: hidden;
    background: var(--page-bg);
    font-family: "Exo 2", sans-serif;
  }
  .business-card {
    position: absolute;
    left: 100px;
    top: 200px;
    width: 1000px;
    height: 567px;
    border-radius: 34px;
    overflow: hidden;
    background: linear-gradient(100deg, var(--card-dark) 0%, var(--card-mid) 45%, var(--card-light) 100%);
    box-shadow: 0 20px 50px rgba(0, 0, 0, 0.25);
  }
  .card-art {
    position: absolute;
    left: 0;
    top: 0;
    width: 1000px;
    height: 567px;
  }
  .contact-details {
    position: absolute;
    left: 40px;
    top: 62px;
    color: var(--text-light);
  }
  .contact-details p { white-space: nowrap; }
  .registration { font-size: 26px; line-height: 38px; color: #d9d9d9; }
  .mobile { margin-top: 18px; font-size: 26px; line-height: 38px; }
  .mobile .label { color: var(--orange); font-weight: 600; }
  .online { font-size: 19px; line-height: 38px; }
  .person {
    position: absolute;
    right: 48px;
    top: 48px;
    text-align: right;
  }
  .person-name { font-size: 36px; font-weight: 700; color: var(--orange); line-height: 44px; }
  .person-role { font-size: 28px; font-weight: 600; color: var(--text-dark); line-height: 36px; }
  .company-name {
    position: absolute;
    left: 42px;
    top: 470px;
    display: flex;
    align-items: center;
    gap: 14px;
    color: var(--orange);
    font-weight: 600;
    font-size: 25px;
    white-space: nowrap;
  }
  .company-name .mark {
    width: 20px;
    height: 20px;
    border-radius: 50%;
    background: var(--orange);
  }
</style>
</head>
<body>
  <div class="business-card">
    <svg class="card-art" viewBox="0 0 1000 567" role="img" aria-label="Orange plug and cord illustration curving down over a dark swoosh">
      <defs>
        <linearGradient id="art-tone" x1="0" y1="0" x2="0.3" y2="1">
          <stop offset="0" stop-color="#f37122" stop-opacity="0.75"/>
          <stop offset="0.45" stop-color="#6a3a1e" stop-opacity="0.8"/>
          <stop offset="1" stop-color="#1c1c1e" stop-opacity="0.95"/>
        </linearGradient>
      </defs>
      <path d="M520 0 L660 0 C650 140 720 190 860 195 C960 200 1000 300 1000 420 L1000 567 L600 567 C630 430 540 300 520 0 Z" fill="url(#art-tone)"/>
    </svg>

    <div class="contact-details">
      <p class="registration">ABN: 71208349162</p>
      <p class="registration">Lic No: 418273D</p>
      <p class="mobile"><span class="label">Mobile :</span> 0481209736</p>
      <p class="online">brent@corvaneelectricalandcomms.example.com.au</p>
      <p class="online">corvaneelectricalandcomms.example.com.au</p>
    </div>

    <div class="person">
      <p class="person-name">Brent Halloway</p>
      <p class="person-role">CEO/Founder</p>
    </div>

    <div class="company-name">
      <span class="mark"></span>
      <span>Corvane Electrical &amp; Communications</span>
    </div>
  </div>
</body>
</html>
```